Marlow Estate Fixers (Handyman / Home Improvement Company)

Looking for a double sided professional looking business card with Logo attached to be highlighted on one side and throwing in an image of a handyman as an option would be nice to see as well. We are a company focused on providing quality Handyman and Home improvement services in a timely manner that is done right the first time with integrity

Industry/Entity Type

Handyman / Home Improvement

Contact Information for Business Card

(LOGO, Name, Mobile and office phone numbers, email) on front side of card, (the words "The SOLUTION to all of your Handyman and Home Improvement needs" followed by "Family Owned and Operated" at the very bottom) on the back.

Colors
EB3D1F
EC4F4E
F09395
F8D3D4
FCEDEE

Requirements
Must have
• Red, Gray, Black Color scheme
Should not have
• No Yellow or Blue colors

```html
<!DOCTYPE html>
<html lang="en">
<head>
<meta charset="utf-8">
<title>Marlow Estate Fixers – Business Card</title>
<link rel="stylesheet" href="https://fonts.googleapis.com/css2?family=Montserrat:wght@400;600;700;800&family=Oswald:wght@500;700&display=swap">
<style>
  :root {
    --stage: #1c1c1c;
    --card-white: #ffffff;
    --brand-red: #e8292e;
    --brand-red-deep: #c81f24;
    --ink: #1a1a1a;
    --ink-soft: #2b2b2b;
    --shadow: rgba(0, 0, 0, 0.55);
    --illus-top: #3a4a8c;
    --illus-bottom: #a5262b;
  }
  * { box-sizing: border-box; margin: 0; padding: 0; }
  html, body { width: 1200px; height: 1059px; overflow: hidden; }
  body {
    background: var(--stage);
    font-family: "Montserrat", Arial, sans-serif;
    position: relative;
  }
  .card {
    position: absolute;
    border-radius: 18px;
    overflow: hidden;
    box-shadow: -6px 6px 14px var(--shadow);
  }

  /* Front side */
  .card-front {
    left: 260px; top: 95px; width: 715px; height: 408px;
    background: var(--card-white);
  }
  .accent-bar {
    position: absolute; left: 0; top: 162px;
    width: 10px; height: 46px;
    background: var(--brand-red);
  }
  .holder-name {
    position: absolute; left: 36px; top: 158px;
    font-size: 28px; font-weight: 700; color: var(--brand-red);
    letter-spacing: 0.3px;
  }
  .holder-role {
    position: absolute; left: 36px; top: 196px;
    font-size: 19px; font-weight: 400; color: var(--ink-soft);
  }
  .contact-list {
    position: absolute; left: 37px; top: 250px;
    list-style: none;
  }
  .contact-item {
    display: flex; align-items: center;
    height: 33.5px;
    font-size: 19px; color: var(--ink);
  }
  .contact-icon { width: 20px; height: 20px; margin-right: 12px; flex: none; }
  .brand-mark-front {
    position: absolute; left: 405px; top: 60px; width: 270px;
    display: flex; align-items: center; gap: 12px;
  }
  .brand-dot {
    width: 26px; height: 26px; border-radius: 50%;
    background: var(--brand-red); flex: none;
  }
  .brand-name {
    font-family: "Montserrat", Arial, sans-serif;
    font-weight: 800; font-size: 26px; line-height: 1.05;
    color: var(--ink); text-transform: uppercase;
  }
  .front-ring {
    position: absolute; left: 338px; top: 225px;
    width: 368px; height: 368px;
    border: 14px solid var(--brand-red);
    border-radius: 50%;
  }

  /* Back side */
  .card-back {
    left: 260px; top: 529px; width: 718px; height: 410px;
    background: var(--brand-red);
  }
  .handyman-illustration {
    position: absolute; left: 25px; top: 21px;
    width: 297px; height: 382px;
    border-radius: 14px;
    background: linear-gradient(180deg, var(--illus-top) 0%, var(--illus-bottom) 100%);
    opacity: 0.85;
  }
  .back-headline {
    position: absolute; left: 340px; top: 10px; width: 318px;
    text-align: center;
    font-family: "Oswald", "Arial Narrow", sans-serif;
    font-weight: 500; font-size: 30px; line-height: 40px;
    color: var(--card-white);
    letter-spacing: -0.5px;
  }
  .back-headline strong { font-weight: 700; }
  .brand-mark-back {
    position: absolute; left: 385px; top: 215px; width: 229px;
    display: flex; align-items: center; gap: 10px;
  }
  .brand-mark-back .brand-dot { background: var(--card-white); }
  .brand-mark-back .brand-name { color: var(--card-white); font-size: 24px; }
  .back-tagline {
    position: absolute; left: 340px; top: 371px; width: 318px;
    text-align: center;
    font-size: 18px; font-weight: 700; color: var(--card-white);
  }
</style>
</head>
<body>

  <section class="card card-front" aria-label="Business card front">
    <div class="front-ring" aria-hidden="true"></div>
    <div class="brand-mark-front">
      <span class="brand-dot" aria-hidden="true"></span>
      <span class="brand-name">Marlow Estate Fixers</span>
    </div>

    <span class="accent-bar" aria-hidden="true"></span>
    <h1 class="holder-name">Daniel Hartley</h1>
    <p class="holder-role">Owner</p>

    <ul class="contact-list">
      <li class="contact-item">
        <svg class="contact-icon" viewBox="0 0 20 20" aria-hidden="true">
          <rect x="5" y="1" width="10" height="18" rx="2" fill="none" stroke="#e8292e" stroke-width="2"/>
          <circle cx="10" cy="15.5" r="1.2" fill="#e8292e"/>
        </svg>
        044-555 018 224
      </li>
      <li class="contact-item">
        <svg class="contact-icon" viewBox="0 0 20 20" aria-hidden="true">
          <path d="M1 7c0-3 4-4 9-4s9 1 9 4v1.5h-4V6.5H5v2H1z" fill="#e8292e"/>
          <path d="M4 10h12l2 8H2z" fill="#e8292e"/>
          <circle cx="10" cy="13.5" r="2" fill="#fff"/>
        </svg>
        044-555 018 224
      </li>
      <li class="contact-item">
        <svg class="contact-icon" viewBox="0 0 20 20" aria-hidden="true">
          <rect x="1" y="4" width="18" height="12" fill="#e8292e"/>
          <path d="M1 4l9 7 9-7" fill="none" stroke="#fff" stroke-width="1.6"/>
        </svg>
        hello@marlowfixers.com
      </li>
    </ul>
  </section>

  <section class="card card-back" aria-label="Business card back">
    <div class="handyman-illustration" role="img" aria-label="Illustration of a smiling handyman in work overalls holding a pipe wrench and a spanner"></div>

    <h2 class="back-headline">
      Your <strong>SOLUTION</strong> to all of your <strong>Handyman</strong> and <strong>Home Improvement Needs</strong>
    </h2>

    <div class="brand-mark-back">
      <span class="brand-dot" aria-hidden="true"></span>
      <span class="brand-name">Marlow Estate Fixers</span>
    </div>

    <p class="back-tagline">Family Owned and Operated</p>
  </section>

</body>
</html>
```